Flat bootstrap design for existing site

I'm looking for a modern flat design based around an existing logo. This has to be a custom design (no external templates), and implemented into a bootstrap framework.

The logo is attached as 2 versions - choose whichever you want, that flows better with whatever design you choose.

Added screenshots of the existing site (currently using the default bootstrap layouts). Please make your designs around those pages in the screenshots (i.e. the homepage only has the postal code input and the header). The active page has 3 screenshots, because I wanted to illustrate the other states that would be visible (in the table rows).

This is a moving/junk removal website, just for some context.

Here's some example websites (flat designs) that I like, just to give you an idea of what I'm after.

https://www.plimvora.com/
https://dacklow.com/
https://trevanu.com/
https://quobrintal.com/en/

Coding

Coded - Design and coding required

Number of Pages Required

5+ page

Colors

Designer to choose colors to be used in the design.

Requirements
Must have
• It must be a modern/simple flat design, that is built around the existing logo (attached).
• It has to be implemented using bootstrap.

```html
<!DOCTYPE html>
<html lang="en">
<head>
<meta charset="utf-8">
<title>Brovak – Booking Details</title>
<link href="https://fonts.googleapis.com/css2?family=Open+Sans:wght@400;600;700&family=Roboto+Condensed:wght@400;700&display=swap" rel="stylesheet">
<style>
  :root{
    --sky-1:#6ccdef;
    --sky-2:#3fb2e2;
    --sky-3:#2e8fcf;
    --accent:#48c6f3;
    --card:#ffffff;
    --card-head:#f5f5f5;
    --line:#e3e3e3;
    --ink:#333333;
    --ink-soft:#555555;
    --row-alt:#f5f5f5;
    --badge:#3d3d3d;
    --footer:#353535;
    --white:#ffffff;
  }
  *{box-sizing:border-box;margin:0;padding:0}
  html,body{width:1159px;height:1200px;overflow:hidden}
  body{
    font-family:"Open Sans",sans-serif;color:var(--ink);
    background:linear-gradient(135deg,var(--sky-1) 0%,var(--sky-2) 45%,var(--sky-3) 100%);
    position:relative;
  }
  .site-header{position:absolute;top:0;left:94px;width:970px;height:110px}
  .brand{position:absolute;left:0;top:40px;display:flex;align-items:center;gap:10px;
    color:var(--white);font-weight:700;font-size:36px;letter-spacing:1px}
  .brand-dot{width:22px;height:22px;border-radius:50%;background:var(--white)}
  .main-nav{position:absolute;right:0;top:40px;display:flex;align-items:center;height:33px;
    font-weight:600;font-size:14px;color:var(--white);text-transform:uppercase}
  .main-nav a{color:inherit;text-decoration:none;margin-left:34px}
  .main-nav .nav-cta{border:2px solid var(--white);border-radius:18px;padding:6px 16px;margin-left:17px}
  .account{margin-left:17px;text-transform:none;font-size:14px;display:flex;align-items:center;gap:10px;margin-top:-10px}
  .card{position:absolute;left:94px;width:970px;background:var(--card);border-radius:2px;
    box-shadow:0 1px 3px rgba(0,0,0,.15)}
  .card-head{height:54px;background:var(--card-head);border-bottom:1px solid var(--line);
    display:flex;align-items:center;justify-content:center;
    font-family:"Roboto Condensed",sans-serif;font-size:20px;color:var(--ink);text-transform:uppercase}
  .booking{top:142px;height:390px}
  .field-label{position:absolute;font-size:13px;color:var(--ink)}
  .control{position:absolute;border:1px solid #dcdcdc;box-shadow:inset 0 1px 2px rgba(0,0,0,.08);
    font-size:11px;color:var(--ink-soft);padding:0 13px;display:flex;align-items:center}
  .control svg{position:absolute}
  .cal-addon{position:absolute;right:0;top:0;width:33px;height:100%;border-left:1px solid #dcdcdc;
    display:flex;align-items:center;justify-content:center}
  .btn-update{position:absolute;left:37px;top:318px;width:125px;height:33px;background:var(--accent);
    color:var(--white);font-size:17px;display:flex;align-items:center;justify-content:center;border:none}
  .drivers{top:572px;height:422px}
  .notice{position:absolute;left:31px;top:95px;width:908px;height:52px;background:var(--accent);
    color:var(--white);font-family:"Roboto Condensed",sans-serif;font-size:16px;
    display:flex;align-items:center;justify-content:center}
  .driver-table{position:absolute;left:31px;top:147px;width:908px;height:235px;
    border:1px solid var(--line);border-top:none;font-family:"Roboto Condensed",sans-serif;font-size:12.5px;color:var(--ink)}
  .tr{position:relative;height:45px}
  .tr.head{height:46px;text-transform:uppercase}
  .tr:nth-child(even){background:var(--row-alt)}
  .td{position:absolute;top:50%;transform:translateY(-50%)}
  .c-name{left:73px}.c-dist{left:236px;margin-top:-3px}.c-time{left:390px}
  .status{right:56px;width:73px;height:26px;background:var(--badge);color:var(--white);
    display:flex;align-items:center;justify-content:center;font-size:12.5px}
  .site-footer{position:absolute;left:0;top:1085px;width:1159px;height:115px;background:var(--footer);
    color:var(--white);text-align:center}
  .copyright{margin-top:27px;font-size:11px;text-transform:uppercase}
  .social{display:flex;justify-content:center;gap:3px;margin-top:12px}
  .social span{width:24px;height:24px;border:1.5px solid var(--white);border-radius:50%}
</style>
</head>
<body>
  <header class="site-header">
    <div class="brand"><span class="brand-dot"></span>BROVAK</div>
    <nav class="main-nav">
      <a href="#">Book</a>
      <a href="#">How it works</a>
      <a href="#" class="nav-cta">Become a driver</a>
      <span class="account">alex@mailbrook.net
        <svg width="8" height="12" viewBox="0 0 8 12"><path d="M4 0L8 5H0zM4 12L0 7h8z" fill="#fff"/></svg>
      </span>
    </nav>
  </header>

  <section class="card booking">
    <div class="card-head">Booking Details</div>
    <label class="field-label" style="left:36px;top:92px">Package Selected:</label>
    <div class="control" style="left:36px;top:122px;width:437px;height:36px">Package 1
      <svg style="right:14px" width="8" height="12" viewBox="0 0 8 12"><path d="M4 0L8 5H0zM4 12L0 7h8z" fill="#444"/></svg>
    </div>
    <label class="field-label" style="left:500px;top:92px">Pick-up time Selected:</label>
    <div class="control" style="left:500px;top:122px;width:437px;height:36px">july 18 at 4:13am
      <span class="cal-addon"><svg width="11" height="11" viewBox="0 0 11 11"><rect x=".5" y="1.5" width="10" height="9" fill="none" stroke="#555"/><path d="M.5 4h10M3 0v3M8 0v3M3.5 4v6.5M7 4v6.5M.5 7h10" stroke="#555"/></svg></span>
    </div>
    <label class="field-label" style="left:36px;top:184px">Description:</label>
    <div class="control" style="left:36px;top:213px;width:901px;height:86px;align-items:flex-start;padding-top:13px">1 large stove
      <svg style="right:478px;top:15px" width="8" height="12" viewBox="0 0 8 12"><path d="M4 0L8 5H0zM4 12L0 7h8z" fill="#444"/></svg>
    </div>
    <button class="btn-update">Update</button>
  </section>

  <section class="card drivers">
    <div class="card-head">Drivers in your area</div>
    <div class="notice">Please stay on this pade and be patient, while we contact drivers and find you one ASP.</div>
    <div class="driver-table">
      <div class="tr head" style="background:#fff">
        <span class="td c-name">Name</span><span class="td c-dist">Distance(km)</span><span class="td c-time" style="margin-top:-3px">Agreed pick-up time</span>
      </div>
      <div class="tr" style="background:var(--row-alt)"><span class="td c-name">Dale Fenwick</span><span class="td c-dist">4.00km away</span><span class="td c-time">–</span><span class="td status">Pending</span></div>
      <div class="tr" style="background:#fff"><span class="td c-name">Owen Marsh</span><span class="td c-dist">5.7km away</span><span class="td c-time">–</span><span class="td status">Pending</span></div>
      <div class="tr" style="background:var(--row-alt)"><span class="td c-name">Reed Calloway</span><span class="td c-dist">11.13km away</span><span class="td c-time">–</span><span class="td status">Pending</span></div>
      <div class="tr" style="background:#fff"><span class="td c-name">Miles Harlan</span><span class="td c-dist">11.91km away</span><span class="td c-time">–</span><span class="td status">Pending</span></div>
    </div>
  </section>

  <footer class="site-footer">
    <p class="copyright">©2017 Brovak, all rights reserved.</p>
    <div class="social"><span></span><span></span><span></span><span></span><span></span></div>
  </footer>
</body>
</html>
```